BRIARWELL TAVERN FRIDAY MAY 3

Flyer design for bar/nightclub event. Trying to keep a general theme with their flyers (see below) but would like to add some neon or some pop to it.

TEXT:

Briarwell Bar & Tavern Presents

LANTERNTIDE NIGHTS
GRAND OPENING EVENT

PURE HOUSE MUSIC W/

MORVEX
TOMAS HALVERO
BENNAR & ACE DRIFTWAY

21+
9PM-130AM
518 M AVENUE DAVIS CA

Target Market(s)

House/dance music crowd.

Industry/Entity Type

Night Club

Font styles to use
Sans Serif

Colors
9bcb3c
fbee3d
ffffff

Requirements
Must have
• Large DJ names
Nice to have
• General theme of the attached flyers. Neon colors that stick with the theme. Anything else that looks cool will be considered

```html
<!DOCTYPE html>
<html lang="en">
<head>
<meta charset="utf-8">
<title>Briarwell Bar &amp; Tavern – Lanterntide Nights Grand Opening</title>
<link rel="stylesheet" href="https://fonts.googleapis.com/css2?family=Anton&family=Roboto+Condensed:wght@700&display=swap">
<style>
  :root {
    --lime: #9bcb3c;
    --neon-yellow: #fbee3d;
    --white: #ffffff;
    --night: #000000;
    --ember: #7a2a10;
    --cream: #fff3a8;
    --ink: #111111;
  }
  * { margin: 0; padding: 0; box-sizing: border-box; }
  html, body { width: 848px; height: 1200px; overflow: hidden; background: var(--night); }
  .flyer {
    position: relative;
    width: 848px;
    height: 1200px;
    overflow: hidden;
    background: linear-gradient(100deg, var(--lime) 0 46%, var(--neon-yellow) 46% 100%);
    font-family: "Roboto Condensed", "Arial Narrow", sans-serif;
  }
  .frame, .banner { position: absolute; inset: 0; width: 848px; height: 1200px; }
  .brand-name {
    position: absolute;
    left: 0; right: 0; top: 150px;
    text-align: center;
    color: var(--white);
    font-weight: 700;
    font-size: 34px;
    letter-spacing: 3px;
  }
  .fire-photo {
    position: absolute;
    left: 90px; top: 300px;
    width: 660px; height: 320px;
    background: radial-gradient(ellipse 42% 48% at 52% 48%, #ffcf6a 0%, #e2691c 30%, #7a1f06 62%, rgba(20,4,0,0) 100%);
  }
  .presents {
    position: absolute;
    left: 192px; top: 486px;
    line-height: 1;
    color: var(--white);
    font-family: "Anton", "Impact", sans-serif;
    font-size: 35px;
    white-space: nowrap;
    transform: rotate(-3deg);
    transform-origin: left center;
    text-shadow: -2px -2px 0 var(--night), 2px -2px 0 var(--night), -2px 2px 0 var(--night), 2px 2px 0 var(--night);
  }
  .event-title {
    position: absolute;
    left: 112px; top: 556px;
    line-height: 1;
    color: var(--ink);
    font-weight: 700;
    font-size: 60px;
    transform: rotate(-3.5deg);
    transform-origin: left center;
    white-space: nowrap;
  }
  .event-subtitle {
    position: absolute;
    left: 308px; top: 617px;
    line-height: 1;
    color: var(--ink);
    font-weight: 700;
    font-size: 45px;
    transform: rotate(2deg);
    transform-origin: left center;
    white-space: nowrap;
  }
  .genre-box {
    position: absolute;
    left: 136px; top: 664px;
    width: 576px; height: 98px;
    background: var(--neon-yellow);
    border-radius: 0 0 10px 10px;
  }
  .genre {
    position: absolute;
    left: 0; right: 0; top: 694px;
    line-height: 1;
    text-align: center;
    font-family: "Anton", "Impact", sans-serif;
    font-size: 54px;
    letter-spacing: 2px;
    color: var(--neon-yellow);
    -webkit-text-stroke: 2px var(--ember);
    paint-order: stroke fill;
    text-shadow: 3px 3px 4px rgba(0,0,0,.45);
  }
  .equalizer {
    position: absolute;
    left: 40px; top: 776px;
    width: 768px; height: 230px;
    background: linear-gradient(180deg, rgba(90,120,20,0) 0%, rgba(150,190,40,.35) 55%, rgba(60,80,10,.15) 100%);
  }
  .lineup-label {
    position: absolute;
    left: 0; right: 0; top: 792px;
    line-height: 1;
    text-align: center;
    font-family: "Anton", "Impact", sans-serif;
    font-size: 31px;
    color: var(--neon-yellow);
  }
  .dj-row {
    position: absolute;
    left: 0; right: 0;
    line-height: 1;
    text-align: center;
    font-family: "Anton", "Impact", sans-serif;
    color: var(--cream);
    -webkit-text-stroke: 3px var(--ember);
    paint-order: stroke fill;
    text-shadow: 3px 3px 3px rgba(0,0,0,.5);
    white-space: nowrap;
  }
  .dj-row--first { top: 846px; font-size: 54px; }
  .dj-row--second { top: 916px; font-size: 44px; }
  .dj-bullet { color: var(--white); margin: 0 14px; }
  .details {
    position: absolute;
    left: 0; right: 0;
    line-height: 1;
    text-align: center;
    font-family: "Anton", "Impact", sans-serif;
    font-size: 44px;
    color: var(--neon-yellow);
    letter-spacing: 1px;
  }
  .details--time { top: 1004px; }
  .details--venue { top: 1058px; }
  .entry {
    position: absolute;
    left: 0; right: 0; top: 1146px;
    line-height: 1;
    text-align: center;
    font-family: "Anton", "Impact", sans-serif;
    font-size: 30px;
    color: var(--ink);
  }
</style>
</head>
<body>
<main class="flyer">
  <svg class="frame" viewBox="0 0 848 1200" aria-hidden="true">
    <polygon fill="var(--lime)" points="0,1100 848,1080 848,1200 0,1200"/>
    <polygon fill="var(--night)" points="40,64 300,40 520,46 800,24 780,120 812,150 792,330 822,540 800,620 832,860 812,1000 830,1080 790,1108 802,1140 760,1160 30,1130 44,1000 14,860 36,700 20,520 40,420 20,300 36,180 16,90"/>
  </svg>

  <div class="brand-name">BRIARWELL BAR &amp; TAVERN</div>

  <div class="fire-photo" role="img" aria-label="Photo of a glowing campfire with burning logs at night"></div>

  <div class="equalizer" role="img" aria-label="Green glowing sound equalizer light pattern"></div>

  <svg class="banner" viewBox="0 0 848 1200" aria-hidden="true">
    <polygon fill="var(--lime)" points="76,548 756,512 704,582 772,604 772,688 304,660 80,662"/>
  </svg>

  <div class="presents">BRIARWELL BAR &amp; TAVERN PRESENTS</div>
  <div class="event-title">LANTERNTIDE NIGHTS</div>
  <div class="event-subtitle">GRAND OPENING EVENT</div>

  <div class="genre-box"></div>
  <div class="genre">PURE HOUSE MUSIC</div>

  <div class="lineup-label">Performed by DJ:</div>
  <div class="dj-row dj-row--first"><span class="dj-bullet">•</span>MORVEX<span class="dj-bullet">•</span>TOMAS HALVERO</div>
  <div class="dj-row dj-row--second"><span class="dj-bullet">•</span>MR. CALDWYN<span class="dj-bullet">•</span>BENNAR &amp; ACE DRIFTWAY</div>

  <div class="details details--time">TIME: 9 pm to 1.30 am</div>
  <div class="details details--venue">VENUE: 518 M AVENUE DAVIS CA</div>

  <div class="entry">ENTRY - Above 21 years of age only</div>
</main>
</body>
</html>
```